Laser Tattoo Removal Business Cards

We are looking for a professional business card design for a laser tattoo removal business. Ideally looking for a black business card design. The name of the business is Brightline Tattoo Removal. We place our cards at local tattoo shops so we ideally are looking for something trendy/edgy to draw both male and female clientele in.

Target Market(s)

Male/Female ages 18-60

Contact Information for Business Card

black background ideally.. hoping to stay within greys, whites and black

Font styles to use
Serif
Sans Serif

Colors
121212
a9a9a9
5c5c5c
f5f5f5
ffffff
7f7f7f
606060
848484
9d9d9d

Requirements
Must have
• Employee Info:
• Melissa Thornbury
• Chief Executive Offer
• m: 919.537.2846
• w: 919.362.4178
• f: 919.685.3907
• mthornbury@brightlinetattooremoval.example
• Address:
• 4615 Oakmere Pkwy, Suite 210
• Raleigh, NC 27654
• Website:
• www.brightlinetattooremoval.example
Nice to have
• Myabe business name on back or logo on back and employee info on the front

```html
<!DOCTYPE html>
<html lang="en">
<head>
<meta charset="utf-8">
<title>Brightline Tattoo Removal – Business Cards</title>
<link rel="stylesheet" href="https://fonts.googleapis.com/css2?family=Roboto:wght@400;500;700&display=swap">
<style>
  :root {
    --stage: #e6e6e6;
    --card-light: #f5f5f5;
    --card-dark: #121212;
    --ink: #121212;
    --ink-soft: #5c5c5c;
    --ink-muted: #9d9d9d;
    --rule: #a9a9a9;
    --white: #ffffff;
  }
  * { box-sizing: border-box; margin: 0; padding: 0; }
  html, body { width: 1200px; height: 960px; overflow: hidden; }
  body {
    position: relative;
    background: var(--stage);
    font-family: "Roboto", Arial, sans-serif;
  }
  .card {
    position: absolute;
    width: 600px;
    height: 343px;
    overflow: hidden;
    box-shadow: 0 2px 6px rgba(0,0,0,0.25);
  }
  .card--front { left: 314px; top: 113px; background: var(--card-light); }
  .card--back  { left: 311px; top: 472px; background: var(--card-dark); }

  .wordmark {
    position: absolute;
    width: 240px;
    text-align: center;
    font-weight: 500;
    line-height: 1;
    white-space: nowrap;
  }
  .wordmark__name { display: block; font-size: 32px; letter-spacing: 2px; }
  .wordmark__tag  { display: block; font-size: 15px; letter-spacing: 2.5px; margin-top: 62px; }
  .card--front .wordmark { left: 28px; top: 128px; color: var(--ink); }
  .card--front .wordmark__tag { color: var(--ink-soft); }
  .card--back .wordmark  { left: 347px; top: 200px; color: var(--white); }

  .divider {
    position: absolute;
    left: 281px; top: 80px;
    width: 1px; height: 192px;
    background: var(--rule);
  }
  .divider::before {
    content: "";
    position: absolute;
    left: -1px; top: 0;
    width: 3px; height: 39px;
    background: var(--ink);
  }

  .contact { position: absolute; left: 309px; top: 76px; width: 280px; color: var(--ink-soft); white-space: nowrap; }
  .contact__name {
    font-size: 21px; font-weight: 700; color: var(--ink);
    letter-spacing: 0.3px; line-height: 24px;
  }
  .contact__title { font-size: 15px; color: var(--ink-muted); line-height: 18px; }
  .contact__address { font-size: 14.5px; line-height: 19px; margin-top: 8px; }
  .contact__list { list-style: none; margin-top: 8px; }
  .contact__item {
    display: flex; align-items: center;
    font-size: 14.5px; line-height: 19.3px;
  }
  .contact__item--long { font-size: 12.2px; }
  .contact__icon { width: 13px; height: 13px; margin-right: 10px; fill: var(--ink); flex: none; }
</style>
</head>
<body>

<section class="card card--front" aria-label="Business card front">
  <div class="wordmark">
    <span class="wordmark__name">BRIGHTLINE</span>
    <span class="wordmark__tag">TATTOO REMOVAL</span>
  </div>

  <div class="divider"></div>

  <div class="contact">
    <h1 class="contact__name">MELISSA THORNBURY</h1>
    <p class="contact__title">Chief Executive Offer</p>
    <p class="contact__address">4615 Oakmere Pkwy, Suite 210<br>Raleigh, NC 27654</p>
    <ul class="contact__list">
      <li class="contact__item">
        <svg class="contact__icon" viewBox="0 0 16 16" aria-hidden="true"><path d="M3.2 1.5l2.4-.4 1.3 3.3-1.6 1.2a9 9 0 0 0 5.1 5.1l1.2-1.6 3.3 1.3-.4 2.4c-.2.8-.9 1.2-1.7 1.2C6.6 13.6 2.4 9.4 2 3.2c0-.8.4-1.5 1.2-1.7z"/></svg>
        919.362.4178
      </li>
      <li class="contact__item">
        <svg class="contact__icon" viewBox="0 0 16 16" aria-hidden="true"><path d="M4.5 0h7A1.5 1.5 0 0 1 13 1.5v13a1.5 1.5 0 0 1-1.5 1.5h-7A1.5 1.5 0 0 1 3 14.5v-13A1.5 1.5 0 0 1 4.5 0zM5 2v10h6V2zm3 11a1 1 0 1 0 0 2 1 1 0 0 0 0-2z"/></svg>
        919.537.2846
      </li>
      <li class="contact__item">
        <svg class="contact__icon" viewBox="0 0 16 16" aria-hidden="true"><path d="M4 1h8v4H4zM1 6h14v7h-3v2H4v-2H1zm4 5v3h6v-3z"/></svg>
        919.685.3907
      </li>
      <li class="contact__item contact__item--long">
        <svg class="contact__icon" viewBox="0 0 16 16" aria-hidden="true"><path d="M1 3h14v10H1zm1.5 1.2V5l5.5 4 5.5-4v-.8z"/></svg>
        mthornbury@brightlinetattooremoval.example
      </li>
      <li class="contact__item">
        <svg class="contact__icon" viewBox="0 0 16 16" aria-hidden="true"><circle cx="8" cy="8" r="7"/><path d="M5 4c2 1 1 3 3 3s1 3 3 3" stroke="#f5f5f5" stroke-width="1.4" fill="none"/></svg>
        www.brightlinetattooremoval.example
      </li>
    </ul>
  </div>
</section>

<section class="card card--back" aria-label="Business card back">
  <div class="wordmark">
    <span class="wordmark__name">BRIGHTLINE</span>
    <span class="wordmark__tag">TATTOO REMOVAL</span>
  </div>
</section>

</body>
</html>
```